Business Cards Design for the electrical wholesaler: clean bold dynamic :)

We need a business card design that would follow our latest brand guidelines. As an electrical wholesaler we want to bring a fresh look and feel into the industry. The design should be clean bold and dynamic. It should come alive with the renewed energy of our green colour. Our grey colour should keep things balanced and complement the notion of maturity and responsibility. We employ Lato as a corporate font however are not bound by this font and we’re open to interpretation here.

Target Market(s)

Electrical contractors

Industry/Entity Type

Business

Contact Information for Business Card

Logo
Name & Surname: Halyna Dorosh
Job Title: Director of Marketing
Email: halya.dorosh@quillmail.example
Cell phone: XXX.XXX.XXXX
Address: 20517 - 87 Ave. Edmonton, AB, Canada. T6K 4N8
Business Phone: 780.555.0184
Website: www.brovix.example

Font styles to use
Other font styles liked:
• Lato

Requirements
Must have
• Logo & website
Nice to have
• Brand elements - some of them you may find in the attached Brand Guidelines (e.g. three lines on the background signifying "W")

```html
<!DOCTYPE html>
<html lang="en">
<head>
<meta charset="utf-8">
<title>Brovix business cards</title>
<link href="https://fonts.googleapis.com/css2?family=Exo+2:wght@500;600&family=Roboto:wght@400;500&display=swap" rel="stylesheet">
<style>
  :root {
    --backdrop: #bdbdbd;
    --green: #7ab62a;
    --green-deep: #62a224;
    --green-shade: rgba(70, 150, 40, 0.45);
    --grey: #4a4d52;
    --text: #3f4246;
    --paper: #f3f3f1;
  }
  * { box-sizing: border-box; margin: 0; padding: 0; }
  html, body { width: 1200px; height: 576px; overflow: hidden; }
  body {
    background: var(--backdrop);
    position: relative;
    font-family: "Roboto", Arial, sans-serif;
  }
  .card {
    position: absolute;
    border-radius: 11px;
    overflow: hidden;
    box-shadow: 0 3px 6px rgba(0,0,0,0.25);
  }
  .card svg.bands { position: absolute; inset: 0; }

  .card--front {
    left: 82px; top: 138px; width: 485px; height: 294px;
    background: linear-gradient(160deg, #80ba22 0%, var(--green) 50%, var(--green-deep) 100%);
  }
  .wordmark {
    position: absolute;
    display: flex; align-items: center; gap: 8px;
    font-family: "Exo 2", "Roboto", sans-serif;
    font-weight: 600;
    color: var(--grey);
    line-height: 1;
  }
  .wordmark__dot { border-radius: 50%; background: var(--grey); }
  .card--front .wordmark { left: 108px; top: 122px; font-size: 54px; }
  .card--front .wordmark__dot { width: 30px; height: 30px; }

  .card--back {
    left: 602px; top: 138px; width: 481px; height: 291px;
    background: var(--paper);
  }
  .card--back .wordmark { left: 18px; top: 30px; font-size: 36px; }
  .card--back .wordmark__dot { width: 20px; height: 20px; }

  .contact { position: absolute; left: 18px; top: 143px; color: var(--text); }
  .contact__name {
    font-family: "Exo 2", "Roboto", sans-serif;
    font-weight: 500; font-size: 21px; color: var(--green); line-height: 1;
  }
  .contact__title { font-size: 12px; margin-top: 4px; }
  .contact__address { font-size: 12px; line-height: 18px; margin-top: 13px; }
  .contact__lines { margin-top: 12px; font-size: 12px; }
  .contact__line { display: flex; align-items: center; gap: 6px; height: 17px; }
  .icon { width: 12px; height: 12px; flex: none; }
  .contact__gap { width: 4px; }
</style>
</head>
<body>

<section class="card card--front" aria-label="Card front">
  <svg class="bands" width="485" height="294" viewBox="0 0 485 294" aria-hidden="true">
    <polygon points="200,55 260,55 360,294 300,294" fill="var(--green-shade)"/>
    <polygon points="300,55 360,55 460,294 400,294" fill="var(--green-shade)"/>
    <polygon points="400,55 460,55 485,115 485,294 500,294" fill="var(--green-shade)"/>
  </svg>
  <div class="wordmark"><span class="wordmark__dot"></span>brovix</div>
</section>

<section class="card card--back" aria-label="Card back">
  <svg class="bands" width="481" height="291" viewBox="0 0 481 291" aria-hidden="true">
    <polygon points="205,0 272,0 392,291 300,291" fill="var(--green)"/>
    <polygon points="310,0 384,0 481,235 481,291 398,291" fill="var(--green)"/>
    <polygon points="420,0 481,0 481,148" fill="var(--green)"/>
  </svg>
  <div class="wordmark"><span class="wordmark__dot"></span>brovix</div>

  <div class="contact">
    <p class="contact__name">Halyna Dorosh</p>
    <p class="contact__title">Founder &amp; CEO</p>
    <p class="contact__address">20517 - 87 Ave. Edmonton,<br>AB, Canada. T6K 4N8</p>
    <div class="contact__lines">
      <p class="contact__line">
        <svg class="icon" viewBox="0 0 12 12" aria-hidden="true"><circle cx="6" cy="6" r="5.5" fill="var(--green)"/><path d="M3.5 5 Q6 3 8.5 5 L8 6.2 L7 5.8 L5 5.8 L4 6.2Z M4.3 6.5 H7.7 V8.5 H4.3Z" fill="#fff"/></svg>
        +1 780.555.0184
      </p>
      <p class="contact__line">
        <svg class="icon" viewBox="0 0 12 12" aria-hidden="true"><circle cx="6" cy="6" r="5.5" fill="var(--green)"/><rect x="3" y="4" width="6" height="4.2" fill="#fff"/><path d="M3 4 L6 6.3 L9 4" stroke="var(--green)" stroke-width="0.7" fill="none"/></svg>
        halya.dorosh@quillmail.example
        <span class="contact__gap"></span>
        <svg class="icon" viewBox="0 0 12 12" aria-hidden="true"><circle cx="6" cy="6" r="5.5" fill="var(--green)"/><circle cx="6" cy="6" r="3" fill="none" stroke="#fff" stroke-width="0.8"/><path d="M3 6 H9 M6 3 V9" stroke="#fff" stroke-width="0.7"/></svg>
        www.brovix.example
      </p>
    </div>
  </div>
</section>

</body>
</html>
```